MRT Property - Business Cards

Looking for a business card & general letterhead, signage etc design for our new logo.

Colours:
000a20
0056a2
00b5ef
0088ce
68cef2

Fonts:
Poppins
Karla

Please keep look and feel of new brand - example in the zip package I sent.

```html
<!DOCTYPE html>
<html lang="en">
<head>
<meta charset="utf-8">
<title>MRT Property Letterhead</title>
<link href="https://fonts.googleapis.com/css2?family=Poppins:wght@400;600&display=swap" rel="stylesheet">
<style>
  :root {
    --backdrop: #8c8c8c;
    --navy: #10152a;
    --paper: #ffffff;
    --brand-blue: #0088ce;
    --sky: #68cef2;
    --ink-light: #f2f4f8;
  }
  * { margin: 0; padding: 0; box-sizing: border-box; }
  html, body {
    width: 1200px;
    height: 686px;
    overflow: hidden;
    background: var(--backdrop);
    font-family: "Poppins", sans-serif;
  }
  .letterhead {
    position: absolute;
    left: 370px;
    top: 18px;
    width: 460px;
    height: 650px;
    background: var(--paper);
    display: flex;
    box-shadow: 0 2px 6px rgba(0,0,0,0.25);
  }
  .side-band {
    width: 134px;
    flex: none;
    height: 100%;
    background: var(--navy);
    display: flex;
    flex-direction: column;
    justify-content: space-between;
    padding: 30px 10px 26px 14px;
    overflow: hidden;
  }
  .brand-name {
    font-weight: 600;
    font-size: 12px;
    color: var(--brand-blue);
    display: flex;
    align-items: center;
    gap: 5px;
    white-space: nowrap;
  }
  .brand-dot {
    width: 8px;
    height: 8px;
    border-radius: 50%;
    background: var(--brand-blue);
    flex: none;
  }
  .contact-block {
    color: var(--ink-light);
    font-size: 7.6px;
    line-height: 1.5;
  }
  .contact-line {
    display: flex;
    align-items: center;
    gap: 5px;
    white-space: nowrap;
  }
  .contact-icon {
    width: 7px;
    height: 7px;
    flex: none;
  }
  .contact-divider {
    height: 1.5px;
    background: var(--sky);
    margin: 9px 0 8px;
    width: 96%;
  }
  .address {
    display: flex;
    gap: 5px;
    align-items: flex-start;
  }
  .address-icon {
    width: 8px;
    height: 10px;
    flex: none;
    margin-top: 1px;
  }
  .address-text { line-height: 1.45; }
  .writing-area { flex: 1; }
</style>
</head>
<body>
  <div class="letterhead">
    <aside class="side-band">
      <div class="brand-name"><span class="brand-dot"></span>MRT Property</div>

      <div class="contact-block">
        <div class="contact-line">
          <svg class="contact-icon" viewBox="0 0 10 10"><path d="M2 1 L4 1 L4.6 3.2 L3.4 4 Q4.4 6 6 6.6 L6.8 5.4 L9 6 L9 8 Q9 9 8 9 Q1 8.6 1 2 Q1 1 2 1Z" fill="var(--sky)"/></svg>
          +61 2 5550 0142
        </div>
        <div class="contact-line">
          <svg class="contact-icon" viewBox="0 0 10 10"><circle cx="5" cy="5" r="4" fill="none" stroke="var(--sky)" stroke-width="1.2"/><path d="M1 5 H9 M5 1 Q2.5 5 5 9 M5 1 Q7.5 5 5 9" fill="none" stroke="var(--sky)" stroke-width="0.9"/></svg>
          www.mrtproperty.com.au
        </div>
        <div class="contact-line">
          <svg class="contact-icon" viewBox="0 0 10 10"><rect x="0.8" y="2" width="8.4" height="6" fill="none" stroke="var(--sky)" stroke-width="1.1"/><path d="M0.8 2 L5 5.4 L9.2 2" fill="none" stroke="var(--sky)" stroke-width="1.1"/></svg>
          info@mrtproperty.com.au
        </div>

        <div class="contact-divider"></div>

        <div class="address">
          <svg class="address-icon" viewBox="0 0 8 10"><path d="M4 0.6 Q7.4 0.6 7.4 3.8 Q7.4 6 4 9.4 Q0.6 6 0.6 3.8 Q0.6 0.6 4 0.6Z" fill="var(--sky)"/><circle cx="4" cy="3.8" r="1.3" fill="var(--navy)"/></svg>
          <div class="address-text">
            Suite 3.14, Block 4<br>
            12 Harbourline Way<br>
            Riverside Park<br>
            NSW 2199
          </div>
        </div>
      </div>
    </aside>
    <main class="writing-area"></main>
  </div>
</body>
</html>
```